Soft Baby Product Needs a new Package/Identity

I need a new package design for a foam Booster Seat called a PLUMVIK. I want the product/brand to be the name of the product; i.e. laminate, tissora, plumvik.

It's a soft foam booster seat for toddlers 3yrs and up. "It's the awesome seat that's "COOL" to sit on, stays put with the weight of a child. Guaranteed to keep a wriggling toddler seated longer or your money back!

Company Name: TotWise USA
Considering: TotWise+Co, TotWiseKIDS, TotWise BATH, TotWiseHOME, etc.

Description for Booster Seat in stores: WISE Plumvik Booster Classic

See previous package attached: Clear Vinyl Carry bag with Handles
and Zipper. The product was visible, however the plastic would
put dents in the foam and would not sit well on the shelves.

I have uploaded a different totwise logo.

I'm looking for an identity/branding in the package; maybe one color per product?
Plumvik: one color logo (see splash of color behind Plumvik on sample box)
Dorvel:  will be another
Etc.

Packaging that can be added to for additional products.

Simple, less is more.  Larger openings. The product
needs to be seen more.

When you go into the store the foam colors will stand out!
It will be known they are TotWise products with Plumvik Foam

Plumvik is a tuff logo.  It is molded into the seats.  It can be one color.
Maybe a stenciled cutout?  Large?  Stenciling is in!
I have uploaded a primary color one.

Reason: I would like more designs before I make a final decision as the payment is guaranteed. I am looking for something that is more open rather than the classic box design. Possibly something similar to a soccer-ball packaging (http://lnk.example-short.net/Qx7Rt2).

Ideas for words:  I will tweak these.

It's the awesome seat that's "COOL" to sit on... 
EVERY child DESERVES a PLUMVIK!

Influenc your little one
to BEHAVE like a big kid!  

A SMART SOLUTION for in-between toddlers!  

POSITIVELY a no-brainer!  Super soft with
supportive sides.. say that 3x!

GOOD BEHAVIOR:...looks like a BIGKID seat!
Transforms your little one into a BIGkid in seconds!

Reason: The box needs to be easily assembled also and hold up in shipping and display....I will comment more

Moms and Dads between the ages of 23 and 35 and grandparents

Plastic

• -The dimensions of the product are 14" x 14" x 6" High, but not a solid, it has ARMS like an 'armbooster' and a sunken seat. Competition has no arms.

-The Box needs to have openings so to FEEL the soft foam. But openings only at the areas where there is foam, not in the seat area, because that would not be visible.

-Openings to show the (6) SIX bright colors: Magenta Pink, LIME green, Blue, Chai Tan, and Onyx Black.

-The product line is kind of like GLIMPS. In other words ALL my products will be of FOAM. Bright Colors. One Piece. Simple design. Very functional thru design. No hard parts, no separate parts/pieces at all. The FOAM is indestructable. ***Our NEW foam.

PLUMVIK is the Softest Foam

-Looking for a box that says PLUMVIK.

-The words could be 3 dimensional, maybe, in the foam material (image/photo) look?

• MODERN design is very popular. At the trade shows there is a modern child area. All the best brands; wemb, ulq, and others are very modern brands.

But I'm looking for something a little edgy!

The box needs coloring that will allow bright colors to PEEK out of the openings, yet leave the package design to say SMART & PLUMVIK.

I would like to capture SMART like the zippa car. TotWise's products are SMART. They create Positive Parenting because they are BEHAVIORIAL AIDS that help parents parent smarter.

Since a booster seat is SOFT and Plumvik the child will want to stay seated longer.

"Little kids learn to Behave like "BIGKIDS"!

But I'm looking for an edgy look and feel!

Maybe instead of my photos, the photos are made into "american anime or illustrated kids, with an endearing look.

Package needs to be 100% recycled - GREEN
GREEN packaging- Is LESS packaging.

No plastic is needed in the windows.

The box needs to be open, to feel the plumvik foam.

• No cutsey Smart stuff; building blocks, graduation hats, etc
Not too much color:

The product design, form, shape and COLOR
needs to stand out.

```html
<!DOCTYPE html>
<html lang="en">
<head>
<meta charset="utf-8">
<title>TotWise Plumvik Booster – Package Panels</title>
<link rel="stylesheet" href="https://fonts.googleapis.com/css2?family=Fredoka:wght@400;600;700&family=Gochi+Hand&family=Short+Stack&display=swap">
<style>
  :root {
    --stage: #e8ebe7;
    --board: #ede3c8;
    --board-edge: #dcd0b1;
    --lime: #7ef40f;
    --lime-deep: #5fd400;
    --lime-text: #7be81a;
    --white: #ffffff;
    --ink: #1b1b1b;
  }
  * { box-sizing: border-box; margin: 0; padding: 0; }
  html, body {
    width: 1200px; height: 1013px; overflow: hidden;
    background: var(--stage);
    font-family: "Fredoka", sans-serif;
  }
  .dieline { position: relative; width: 1200px; height: 1013px; }

  .panel {
    position: absolute;
    background: var(--board);
    border: 1px solid var(--board-edge);
    overflow: hidden;
  }
  .panel--top   { left: 40px;  top: 30px;  width: 720px; height: 580px; }
  .panel--front { left: 40px;  top: 630px; width: 720px; height: 350px; }
  .panel--side  { left: 780px; top: 630px; width: 380px; height: 350px; }

  /* brand splash */
  .splash {
    position: absolute; background: var(--lime); border-radius: 50%;
    display: flex; flex-direction: column; align-items: center; justify-content: center;
    color: var(--white); text-align: center;
  }
  .panel--top .splash { left: -60px; top: -200px; width: 560px; height: 520px; padding-top: 190px; }
  .brand-name { font-family: "Fredoka", sans-serif; font-weight: 400; color: var(--white); letter-spacing: 1px; }
  .product-name { font-family: "Fredoka", sans-serif; font-weight: 700; color: var(--white); line-height: .9; }
  .panel--top .brand-name { font-size: 34px; margin-bottom: 4px; }
  .panel--top .product-name { font-size: 96px; }

  .panel--side .splash { left: 40px; top: 60px; width: 300px; height: 230px; }
  .panel--side .brand-name { font-size: 22px; margin-bottom: 2px; }
  .panel--side .product-name { font-size: 52px; }

  /* tagline block */
  .tagline {
    position: absolute; left: 180px; top: 336px; white-space: nowrap;
    font-family: "Gochi Hand", cursive; font-size: 24px; line-height: 1; color: var(--lime-text);
  }
  .headline {
    position: absolute; left: 180px; top: 370px; white-space: nowrap;
    font-family: "Short Stack", cursive; font-size: 62px; color: var(--lime-text);
    letter-spacing: 3px; line-height: 1;
  }

  .badge {
    position: absolute; left: 555px; top: 330px; width: 140px; height: 140px;
    border-radius: 50%; background: var(--lime);
    display: flex; flex-direction: column; align-items: center; justify-content: center;
  }
  .badge__seat { width: 64px; height: 44px; margin-bottom: 6px; }
  .badge__label { font-family: "Fredoka", sans-serif; font-weight: 600; font-size: 20px; color: var(--ink); line-height: 1; }
  .badge__age { font-family: "Fredoka", sans-serif; font-size: 12px; color: var(--ink); }

  .fine-print {
    position: absolute; font-family: "Fredoka", sans-serif; font-size: 11px;
    line-height: 1.35; color: var(--lime-deep);
  }
  .fine-print p + p { margin-top: 8px; }
  .fine-print--features { left: 180px; top: 458px; width: 250px; text-align: center; }
  .fine-print--details { left: 555px; top: 482px; width: 150px; text-align: left; }

  /* viewing window */
  .window {
    position: absolute; left: 60px; top: 40px; width: 200px; height: 240px;
    border-radius: 50%;
    background: radial-gradient(circle at 45% 40%, #74ec14, #5fd300);
  }
  .sign-off {
    position: absolute; left: 60px; top: 294px; white-space: nowrap;
    font-family: "Short Stack", cursive; font-size: 28px; line-height: 1.2; color: var(--lime-text);
  }
</style>
</head>
<body>
<main class="dieline">

  <section class="panel panel--top" aria-label="Top panel">
    <div class="splash">
      <span class="brand-name">TotWise</span>
      <h1 class="product-name">Plumvik<br>Booster</h1>
    </div>

    <p class="tagline">little kids learn to behave like</p>
    <p class="headline">BIG KIDS</p>

    <div class="badge">
      <svg class="badge__seat" viewBox="0 0 64 44" role="img" aria-label="Outline of the classic foam booster seat">
        <rect x="0" y="0" width="64" height="44" rx="8" fill="#ffffff"/>
      </svg>
      <span class="badge__label">CLASSIC</span>
      <span class="badge__age">Ages 2.5 and up</span>
    </div>

    <div class="fine-print fine-print--features">
      <p>Soft ribbed foam<br>pattern is slip resistant</p>
      <p>100% recyclable<br>Durable material. Non allergenic.<br>No latex. No phthalates.</p>
    </div>
    <div class="fine-print fine-print--details">
      <p>Sleek, low back cozy design for comfort and stability</p>
      <p>Unique molded foam stays put with weight of child</p>
    </div>
  </section>

  <section class="panel panel--front" aria-label="Front panel">
    <div class="window" role="img" aria-label="Open window showing the lime green foam seat inside"></div>
    <p class="sign-off">feels... super soft</p>
  </section>

  <section class="panel panel--side" aria-label="Side panel">
    <div class="splash">
      <span class="brand-name">TotWise</span>
      <h2 class="product-name">Plumvik<br>Booster</h2>
    </div>
  </section>

</main>
</body>
</html>
```